Veltrane Group Business Card Design

The CEO is looking for a new trendy look for his business card.
You can stay with current branding or come up with something new/creative. It can be 3D, including Medical Office buildings. You can use our logo in a variety of colors. Please include name, title, company name, company website, email address, cell number

Target Market(s)

Real Estate Development and Construction

Industry/Entity Type

Health care real estate

Contact Information for Business Card

Rohesh Kamdar, CEO M-604.781.2249 E-roheshkamdar@veltrane.com Address:4180 Lindqvist Ave, Tampa, FL 33482 www.veltrane.com

Font styles to use
Other font styles liked:
• Be creative

Requirements
Must have
• Creative, trendy look
Nice to have
• Please go to our website to get a feel- www. veltrane.com
Should not have
• small fonts

```html
<!DOCTYPE html>
<html lang="en">
<head>
<meta charset="utf-8">
<title>Veltrane Group Business Card</title>
<link rel="stylesheet" href="https://fonts.googleapis.com/css2?family=Poppins:wght@300;400;700;800&display=swap">
<style>
  :root {
    --page-bg: #2a2a2a;
    --card-red: #b31f2b;
    --ink: #ffffff;
    --frame-line: rgba(255,255,255,0.85);
  }
  * { margin: 0; padding: 0; box-sizing: border-box; }
  html, body { width: 1200px; height: 1015px; overflow: hidden; }
  body {
    background: var(--page-bg);
    font-family: "Poppins", sans-serif;
    color: var(--ink);
    position: relative;
  }
  .card {
    position: absolute;
    left: 220px;
    width: 760px;
    height: 434px;
    background: var(--card-red);
    box-shadow: 0 10px 30px rgba(0,0,0,0.45);
  }
  .card--front { top: 50px; }
  .card--back { top: 531px; }
  .card-frame { position: absolute; inset: 0; width: 760px; height: 434px; }
  .brand-name {
    position: absolute;
    inset: 0;
    display: flex;
    align-items: center;
    justify-content: center;
    font-weight: 800;
    font-size: 74px;
    letter-spacing: -2px;
    white-space: nowrap;
  }
  .identity {
    position: absolute;
    top: 140px;
    left: 40px;
    right: 40px;
    display: flex;
    align-items: center;
    justify-content: center;
    gap: 22px;
    white-space: nowrap;
  }
  .person { text-align: right; }
  .person-name { font-weight: 700; font-size: 34px; line-height: 1.1; }
  .person-title { font-weight: 300; font-size: 18px; line-height: 1.1; }
  .divider { width: 1px; height: 84px; background: var(--frame-line); }
  .contact-list { list-style: none; display: flex; flex-direction: column; gap: 4px; }
  .contact-item {
    display: flex; align-items: center; gap: 9px;
    font-weight: 300; font-size: 16px; line-height: 1.35;
  }
  .contact-icon { width: 16px; height: 16px; flex: none; }
  .address {
    position: absolute;
    left: 40px; right: 40px; bottom: 78px;
    display: flex; justify-content: center; align-items: center; gap: 10px;
    font-weight: 400; font-size: 20px;
    white-space: nowrap;
  }
</style>
</head>
<body>

<section class="card card--front" aria-label="Card front">
  <svg class="card-frame" viewBox="0 0 760 434" aria-hidden="true">
    <g stroke="var(--frame-line)" stroke-width="1" fill="none">
      <path d="M365 30 H30 V404 H365"/>
      <path d="M395 30 H730 V404 H395"/>
    </g>
    <rect x="376" y="25" width="9" height="9" fill="var(--ink)"/>
    <rect x="376" y="399" width="9" height="9" fill="var(--ink)"/>
  </svg>
  <div class="brand-name">Veltrane Group</div>
</section>

<section class="card card--back" aria-label="Card back">
  <svg class="card-frame" viewBox="0 0 760 434" aria-hidden="true">
    <g stroke="var(--frame-line)" stroke-width="1" fill="none">
      <path d="M365 30 H30 V404 H365"/>
      <path d="M395 30 H730 V404 H395"/>
    </g>
    <rect x="376" y="25" width="9" height="9" fill="var(--ink)"/>
    <rect x="376" y="399" width="9" height="9" fill="var(--ink)"/>
  </svg>

  <div class="identity">
    <div class="person">
      <div class="person-name">Rohesh Kamdar</div>
      <div class="person-title">CEO</div>
    </div>
    <div class="divider"></div>
    <ul class="contact-list">
      <li class="contact-item">
        <svg class="contact-icon" viewBox="0 0 24 24" aria-hidden="true"><path fill="var(--ink)" d="M6.6 10.8a15.1 15.1 0 0 0 6.6 6.6l2.2-2.2a1 1 0 0 1 1-.25 11.4 11.4 0 0 0 3.6.57 1 1 0 0 1 1 1V20a1 1 0 0 1-1 1A17 17 0 0 1 3 4a1 1 0 0 1 1-1h3.5a1 1 0 0 1 1 1c0 1.250.2 2.450.57 3.57a1 1 0 0 1-.25 1z"/></svg>
        604.781.2249
      </li>
      <li class="contact-item">
        <svg class="contact-icon" viewBox="0 0 24 24" aria-hidden="true"><path fill="var(--ink)" d="M2 5h20v14H2zm2 2v.5l8 5 8-5V7z"/></svg>
        roheshkamdar@veltrane.com
      </li>
      <li class="contact-item">
        <svg class="contact-icon" viewBox="0 0 24 24" aria-hidden="true"><g fill="none" stroke="var(--ink)" stroke-width="2"><circle cx="12" cy="12" r="9"/><path d="M3 12h18M12 3c3 3 3 15 0 18M12 3c-3 3-3 15 0 18"/></g></svg>
        www.veltrane.com
      </li>
    </ul>
  </div>

  <div class="address">
    <svg class="contact-icon" viewBox="0 0 24 24" aria-hidden="true"><path fill="var(--ink)" d="M12 2a7 7 0 0 0-7 7c0 5 7 13 7 13s7-8 7-13a7 7 0 0 0-7-7zm0 9.5A2.5 2.5 0 1 1 12 6.5a2.5 2.5 0 0 1 0 5z"/></svg>
    4180 Lindqvist Ave, Tampa, FL 33482
  </div>
</section>

</body>
</html>
```